Redesign Website - Current one too plain

The description is in the uploaded file. Please let me know if you need any more information. I'd prefer it if someone could implement the design to a WordPress site but the best design will win, regardless.
I would like the forms to look nice as well
UPDATE:
I don't think we can use the images that I provided, I think they make the site look a bit 'cheap' and I really don't know how to replace them. One thought I have had is to make the "Simple, Unique, Effective" a second feature on the right side of the page with the search on the left
Target Market(s)
Small companies, private sellers of cars and people who rent their caravan/holiday home out
Industry/Entity Type
Advertising
Number of Pages Required
3 page
Colors
Designer to choose colors to be used in the design.
Look and feel
Each slider illustrates characteristics of the customer's brand and the style your logo design should communicate.

```html
<!DOCTYPE html>
<html lang="en">
<head>
<meta charset="utf-8">
<title>Zapdot — Welcome</title>
<link rel="stylesheet" href="https://fonts.googleapis.com/css2?family=Roboto:wght@400;500;700;900&display=swap">
<style>
:root{
  --lime:#dfff00;
  --lime-soft:#e8ff3a;
  --ink:#2d2d2d;
  --ink-deep:#101010;
  --paper:#ffffff;
  --muted:#6b6b6b;
  --field:#e3e3e3;
  --line:#eeeeee;
}
*{box-sizing:border-box;margin:0;padding:0}
html,body{width:1200px;height:4000px;overflow:hidden}
body{position:relative;background:var(--paper);font-family:"Roboto",Arial,sans-serif;color:var(--ink)}
.abs{position:absolute}
.bands{position:absolute;left:0;top:0;width:1200px;height:4000px}
.topline{left:0;top:0;width:1200px;height:4px;background:var(--lime)}

.brand{display:flex;align-items:center;gap:14px;color:var(--lime);font-weight:700;font-size:34px;letter-spacing:6px}
.brand .dot{width:30px;height:30px;border-radius:50%;background:var(--lime)}
.site-brand{left:112px;top:62px}

.nav{top:72px;display:flex;gap:0;color:#fff;font-size:16px;font-weight:500}
.nav span{position:absolute;white-space:nowrap}
.login{left:959px;top:62px;width:112px;height:42px;border-radius:21px;background:var(--lime);color:var(--ink);font-size:17px;font-weight:500;display:flex;align-items:center;padding-left:22px}
.login .user{position:absolute;right:5px;top:5px;width:32px;height:32px;border-radius:50%;background:var(--ink);border:2px solid #fff}

.hero-title{left:112px;top:222px;color:#fff;font-weight:900;font-size:64px;line-height:84px;letter-spacing:1px}
.plate{top:415px;height:50px;width:50px;background:var(--lime);color:var(--ink);font-weight:900;font-size:34px;display:flex;align-items:center;justify-content:center;border-radius:3px}
.spin{color:#fff;font-size:13px;line-height:9px;text-align:center}
.chip{top:516px;height:40px;border-radius:20px;font-size:16px;font-weight:500;display:flex;align-items:center;justify-content:center;border:2px solid #fff;color:#fff}
.chip.on{background:#fff;color:var(--ink)}
.search-btn{left:464px;top:516px;width:162px;height:40px;border-radius:20px;background:var(--lime);color:var(--ink);font-size:16px;font-weight:500;display:flex;align-items:center;padding-left:20px}
.round{position:absolute;border-radius:50%;background:var(--ink);display:flex;align-items:center;justify-content:center}
.hero-visual{left:465px;top:160px;width:735px;height:485px;background:linear-gradient(135deg,#d8d8d4 0%,#b9b8b2 45%,#7d7d7f 100%);clip-path:polygon(30% 0,100% 0,100% 100%,0 100%,0 60%,30% 35%)}

.section-title{font-weight:900;font-size:46px;display:flex;align-items:center;gap:22px;white-space:nowrap}
.section-title .mark{width:34px;height:34px;border-radius:50%;background:var(--ink)}
.why-title{left:386px;top:780px}

.feature{width:272px;text-align:center}
.feature .icon{width:118px;height:118px;border-radius:50%;background:var(--ink);margin:0 auto;display:flex;align-items:center;justify-content:center}
.feature .icon i{width:58px;height:58px;border-radius:50%;background:var(--lime);display:flex;align-items:center;justify-content:center}
.feature h3{font-size:19px;font-weight:700;margin-top:24px;letter-spacing:.5px}
.feature p{font-size:12px;color:var(--muted);line-height:24px;margin:8px auto 0;width:190px}
.feature.raised{background:#fff;box-shadow:0 6px 22px rgba(0,0,0,.12);padding-top:44px;height:326px}
.feature.raised .icon{background:var(--lime)}
.feature.raised .icon i{background:var(--ink)}
.feature.raised .corner{position:absolute;right:0;bottom:0;width:46px;height:70px;border-right:12px solid var(--lime);border-bottom:12px solid var(--lime);border-bottom-right-radius:22px}

.about-title{left:110px;top:1590px;color:#fff}
.about-title .mark{background:var(--lime)}
.about-copy{left:110px;top:1670px;width:430px;color:#fff;font-size:13px;line-height:27.5px}
.about-copy p+p{margin-top:27px}
.about-orb{left:640px;top:1520px;width:400px;height:400px;border-radius:50%;background:var(--lime)}
.pill{height:42px;border-radius:21px;background:var(--lime);color:var(--ink);font-size:16px;font-weight:500;display:flex;align-items:center;padding-left:22px}
.pill .round{right:4px;top:4px;width:34px;height:34px}
.read-more{left:110px;top:1945px;width:151px}

.cust-title{left:300px;top:2200px}
.cust-lead{left:150px;top:2280px;width:900px;text-align:center;font-size:14.5px;line-height:29px;color:var(--muted)}
.quote-card{top:2387px;width:461px;height:321px;background:#fff;box-shadow:0 4px 20px rgba(0,0,0,.10);padding:38px 40px 0 41px}
.quote-card .qm{color:var(--lime);font-size:86px;font-weight:900;line-height:60px;height:48px;letter-spacing:-6px}
.quote-card p{font-size:13px;color:var(--muted);line-height:25.8px;margin-top:6px}
.quote-card .who{font-size:15.5px;font-weight:700;color:var(--ink-deep);text-decoration:underline;margin-top:20px}
.arrow-btn{top:2756px;width:38px;height:38px;border-radius:50%;display:flex;align-items:center;justify-content:center;font-size:14px}
.arrow-btn.prev{left:558px;background:#fff;box-shadow:0 2px 8px rgba(0,0,0,.15);color:var(--muted)}
.arrow-btn.next{left:604px;background:var(--ink);color:#fff}

.contact-panel{left:123px;top:2888px;width:459px;height:534px;border-radius:18px;background:linear-gradient(160deg,#e6ff1a 0%,#d4f000 55%,#c6e200 100%);overflow:hidden}
.contact-panel .photo{position:absolute;left:0;top:0;width:100%;height:100%;background:radial-gradient(ellipse at 45% 40%,rgba(150,170,0,.45),rgba(0,0,0,0) 62%)}
.contact-title{left:50px;top:88px;font-size:44px;font-weight:900;line-height:56px;color:var(--ink-deep);display:flex;gap:20px}
.contact-title .mark{width:34px;height:34px;border-radius:50%;background:var(--ink-deep);margin-top:12px;flex:none}
.contact-copy{left:50px;top:230px;width:360px;text-align:center;font-size:14.5px;line-height:29px;color:var(--ink)}
.get-started{left:153px;top:405px;width:151px;background:var(--ink);color:#fff}
.get-started .round{background:var(--lime)}

.quote-form-title{left:641px;top:2922px;font-size:28px;font-weight:700;line-height:41px;color:var(--ink-deep)}
.field{height:42px;background:var(--field);font-size:12.5px;color:#7a7a7a;padding:15px 20px 0}
.field.area{height:154px}
.submit{left:911px;top:3338px;width:163px}

.site-footer{left:0;top:3542px;width:1200px;height:458px;background:var(--ink-deep)}
.footer-orb{left:470px;top:3660px;width:200px;height:200px;border-radius:50%;background:#1f1f1f}
.footer-brand{left:426px;top:3602px;font-size:42px;letter-spacing:8px}
.footer-brand .dot{width:40px;height:40px}
.news-title{left:157px;top:3708px;color:#fff;font-size:27px;font-weight:700}
.news-field{top:3702px;width:154px;height:42px;border-radius:21px;background:#fff;font-size:11.5px;color:#555;padding:14px 0 0 24px}
.news-btn{left:888px;top:3702px;width:153px;height:42px;border-radius:21px;background:var(--lime);color:var(--ink);font-weight:700;font-size:16px;display:flex;align-items:center;justify-content:center}
.info{top:3795px;color:#fff;font-size:14px;display:flex;align-items:center;gap:10px;white-space:nowrap}
.sep{color:#fff;font-size:14px}
.fnav{top:3856px;color:#fff;font-size:14px;white-space:nowrap}
.social{top:3906px;width:28px;height:28px;border-radius:50%;background:var(--lime)}
.copyright{left:0;top:3954px;width:1200px;text-align:center;color:#fff;font-size:11px}
</style>
</head>
<body>

<svg class="bands" viewBox="0 0 1200 4000" aria-hidden="true">
  <polygon points="0,0 1200,0 1200,638 0,717" fill="#2d2d2d"/>
  <polygon points="0,1510 1200,1342 1200,1983 0,2139" fill="#2d2d2d"/>
</svg>
<div class="abs topline"></div>

<header>
  <div class="abs brand site-brand"><span class="dot"></span>ZAPDOT.com</div>
  <nav class="abs nav" style="left:0">
    <span style="left:494px">Home</span>
    <span style="left:594px">Advertise</span>
    <span style="left:720px">Contact Us</span>
    <span style="left:858px">Register</span>
  </nav>
  <div class="abs login">Login<span class="user"></span></div>
</header>

<section class="hero">
  <div class="abs hero-visual" role="img" aria-label="Photo of a static caravan, an SUV and a company van, each showing a short code plate"></div>
  <h1 class="abs hero-title">WELCOME TO<br>ZAPDOT</h1>
  <div class="abs spin" style="left:108px;top:431px">&#8963;<br>&#8964;</div>
  <div class="abs plate" style="left:135px">A</div>
  <div class="abs plate" style="left:203px">1</div>
  <div class="abs spin" style="left:264px;top:431px">&#8963;<br>&#8964;</div>
  <div class="abs chip on" style="left:112px;width:84px">Car</div>
  <div class="abs chip" style="left:219px;width:104px">Caravan</div>
  <div class="abs chip" style="left:341px;width:104px">Company</div>
  <div class="abs search-btn">Search Now
    <span class="round" style="right:4px;top:4px;width:32px;height:32px">
      <svg width="14" height="14" viewBox="0 0 14 14"><circle cx="6" cy="6" r="4.2" fill="none" stroke="#fff" stroke-width="1.6"/><line x1="9" y1="9" x2="12.5" y2="12.5" stroke="#fff" stroke-width="1.6"/></svg>
    </span>
  </div>
</section>

<section class="why">
  <h2 class="abs section-title why-title"><span class="mark"></span>WHY CHOOSE US</h2>
  <div class="abs feature" style="left:162px;top:932px">
    <div class="icon"><i><svg width="30" height="30" viewBox="0 0 30 30"><circle cx="15" cy="15" r="10" fill="none" stroke="#2d2d2d" stroke-width="2"/><path d="M10 15l4 4 7-8" fill="none" stroke="#2d2d2d" stroke-width="2"/></svg></i></div>
    <h3>SIMPLE</h3>
    <p>Create &nbsp;your advert and display your code</p>
  </div>
  <div class="abs feature raised" style="left:464px;top:928px">
    <div class="icon"><i><svg width="30" height="30" viewBox="0 0 30 30"><circle cx="13" cy="13" r="8" fill="none" stroke="#fff" stroke-width="2"/><line x1="19" y1="19" x2="25" y2="25" stroke="#fff" stroke-width="2.4"/></svg></i></div>
    <h3>UNIQUE</h3>
    <p>Customers find you by an easy-to-remember code</p>
    <span class="corner"></span>
  </div>
  <div class="abs feature" style="left:766px;top:932px">
    <div class="icon"><i><svg width="30" height="30" viewBox="0 0 30 30"><path d="M6 22l6-6 4 4 8-9" fill="none" stroke="#2d2d2d" stroke-width="2"/><path d="M19 11h5v5" fill="none" stroke="#2d2d2d" stroke-width="2"/></svg></i></div>
    <h3>EFFECTIVE</h3>
    <p>Customers are directed to you and not a list of your competitors</p>
  </div>
</section>

<section class="about">
  <div class="abs about-orb"></div>
  <h2 class="abs section-title about-title"><span class="mark"></span>ABOUT US</h2>
  <div class="abs about-copy">
    <p>I must explain to you how all this mistaken idea of denouncing pleasure and praising pain was born and I will give you a complete account of the system, and expound the actual teachings of the great explorer of the truth, the master-builder of human happiness. No one rejects, dislikes, or avoids pleasure itself</p>
    <p>&nbsp;or desires to obtain pain of itself, because it is pain, but because occasionally circumstances occur in which toil and pain can procure him some great pleasure.</p>
  </div>
  <div class="abs pill read-more">Read More
    <span class="round"><svg width="14" height="12" viewBox="0 0 14 12"><path d="M1 6h11M8 2l4 4-4 4" fill="none" stroke="#fff" stroke-width="1.8"/></svg></span>
  </div>
</section>

<section class="customers">
  <h2 class="abs section-title cust-title"><span class="mark"></span>OUR HAPPY CUSTOMERS</h2>
  <p class="abs cust-lead">I must explain to you how all this mistaken idea of denouncing pleasure and praising pain was born and I will give you a complete account of the system, and expound the actual teachings of the great explorer of the truth, the master</p>
  <article class="abs quote-card" style="left:116px">
    <div class="qm">&rdquo;</div>
    <p>I must explain to you how all this mistaken idea of denouncing pleasure and praising pain was born and I will give you a complete account of the system, and expound the actual teachings of the great explorer of the truth, the master-builder of human happiness. No one rejects, dislikes, or avoids pleasure itself, because it is pleasure</p>
    <div class="who">Owen Carter</div>
  </article>
  <article class="abs quote-card" style="left:622px">
    <div class="qm">&rdquo;</div>
    <p>I must explain to you how all this mistaken idea of denouncing pleasure and praising pain was born and I will give you a complete account of the system, and expound the actual teachings of the great explorer of the truth, the master-builder of human happiness. No one rejects, dislikes, or avoids pleasure itself, because it is pleasure</p>
    <div class="who">Liam Porter</div>
  </article>
  <div class="abs arrow-btn prev">&larr;</div>
  <div class="abs arrow-btn next">&rarr;</div>
</section>

<section class="contact">
  <div class="abs contact-panel">
    <div class="photo" role="img" aria-label="Lime-tinted photo of a smiling woman at a desk"></div>
    <h2 class="abs contact-title"><span class="mark"></span><span>GET IN TOUCH<br>WITH US</span></h2>
    <p class="abs contact-copy">I must explain to you how all this mistaken idea of denouncing pleasure and praising pain was born and I will give you a complete account of the system, and expound the actual teachings of the great explorer of the truth</p>
    <div class="abs pill get-started">Get Started
      <span class="round"><svg width="14" height="12" viewBox="0 0 14 12"><path d="M1 6h11M8 2l4 4-4 4" fill="none" stroke="#2d2d2d" stroke-width="1.8"/></svg></span>
    </div>
  </div>

  <h3 class="abs quote-form-title">Submit Your Request for a Free<br>Quote</h3>
  <div class="abs field" style="left:642px;top:3028px;width:207px">First Name</div>
  <div class="abs field" style="left:871px;top:3028px;width:206px">Last Name</div>
  <div class="abs field" style="left:642px;top:3090px;width:207px">Email Address</div>
  <div class="abs field" style="left:871px;top:3090px;width:206px">Contact Number</div>
  <div class="abs field area" style="left:642px;top:3152px;width:435px">Your Message Goes Here....</div>
  <div class="abs pill submit">Submit Here
    <span class="round"><svg width="14" height="12" viewBox="0 0 14 12"><path d="M1 6h11M8 2l4 4-4 4" fill="none" stroke="#fff" stroke-width="1.8"/></svg></span>
  </div>
</section>

<footer>
  <div class="abs site-footer"></div>
  <div class="abs footer-orb"></div>
  <div class="abs brand footer-brand"><span class="dot"></span>ZAPDOT.com</div>
  <h3 class="abs news-title">Subscribe Our Newsletter</h3>
  <div class="abs news-field" style="left:545px">Full Name</div>
  <div class="abs news-field" style="left:715px">Email Address</div>
  <div class="abs news-btn">Subscribe</div>

  <div class="abs info" style="left:223px">
    <svg width="16" height="20" viewBox="0 0 16 20"><path d="M8 1a6.5 6.5 0 0 0-6.5 6.5C1.5 12 8 19 8 19s6.5-7 6.5-11.5A6.5 6.5 0 0 0 8 1z" fill="#dfff00"/><circle cx="8" cy="7.5" r="2.4" fill="#101010"/></svg>
    22Y, Zapdot , Lorem lisum 654 543</div>
  <span class="abs sep" style="left:519px;top:3795px">|</span>
  <div class="abs info" style="left:582px">
    <svg width="16" height="16" viewBox="0 0 16 16"><path d="M3 1l3 3-1.5 2a9 9 0 0 0 5 5L11.5 9.5l3 3-2 2.5C6 14 1.5 9 1 3z" fill="#dfff00"/></svg>
    +1 555 010 0199</div>
  <span class="abs sep" style="left:769px;top:3795px">|</span>
  <div class="abs info" style="left:832px">
    <svg width="16" height="12" viewBox="0 0 16 12"><rect x="0.5" y="0.5" width="15" height="11" fill="#dfff00"/><path d="M1 1l7 6 7-6" fill="none" stroke="#101010" stroke-width="1.2"/></svg>
    admin@zapdot.com</div>

  <span class="abs fnav" style="left:260px">Home</span>
  <span class="abs sep" style="left:350px;top:3856px">|</span>
  <span class="abs fnav" style="left:404px">Advertise</span>
  <span class="abs sep" style="left:516px;top:3856px">|</span>
  <span class="abs fnav" style="left:570px">Contact Us</span>
  <span class="abs sep" style="left:692px;top:3856px">|</span>
  <span class="abs fnav" style="left:746px">Register</span>
  <span class="abs sep" style="left:850px;top:3856px">|</span>
  <span class="abs fnav" style="left:904px">Login</span>

  <span class="abs social" style="left:548px"></span>
  <span class="abs social" style="left:585px"></span>
  <span class="abs social" style="left:622px"></span>
  <p class="abs copyright">&copy; Copyright 2023 | All Rights Reserved.</p>
</footer>

</body>
</html>
```